Dermal Care Nursing Circle - Rack Card Design

This is a 2-sided rack card that should be 3.5 inches wide by 8.5 inches tall.

Text (with instructions), logo and website image are attached. For the main image on the front, you can use the attached image, or pull whatever you like off of pictovault.example, and we will purchase the photo from the winning design

The front should have text plus a nurse image, the back should have mostly text with the website image and legend.
Updates

We have received many high quality designs, but it is apparent to us that at the print size we are currently using (3.5x8.5), that the image of the homepage on the back is too small, and not legible. As such, we have decided that we would like to go with a horizontal version at 8.5 wide by 5.5 tall, with a larger more legible version of the website on the back and call outs to one side or the other, please resubmit your designs in that format. Thank you, and sorry for the inconvenience. Ned

Industry/Entity Type

Nurse

Font styles to use
Sans Serif

Colors
876aae
6b449b
b7a5cd
e4daeb

Requirements
Must have
• Please use the color palate from the attached logo, and a nursing image on the front.

```html
<!DOCTYPE html>
<html lang="en">
<head>
<meta charset="utf-8">
<title>Dermal Care Nursing Circle – Rack Card</title>
<link rel="stylesheet" href="https://fonts.googleapis.com/css2?family=Jost:wght@400;500&family=Didact+Gothic&display=swap">
<style>
  :root{
    --purple:#6b449b;
    --purple-mid:#876aae;
    --lilac:#b7a5cd;
    --lilac-pale:#e4daeb;
    --ink:#2d2d2d;
    --text:#3c3c3c;
    --row:#e6e6e6;
    --row-alt:#ececec;
    --white:#ffffff;
    --stage:#2a2a2a;
  }
  *{box-sizing:border-box;margin:0;padding:0}
  html,body{width:1200px;height:960px;overflow:hidden;background:var(--stage)}
  body{position:relative;font-family:"Didact Gothic",sans-serif;color:var(--text)}

  .card{position:absolute;width:373px;height:904px;background:var(--white);overflow:hidden}
  .card--front{left:210px;top:29px}
  .card--back{left:615px;top:27px}

  /* lockup */
  .lockup{display:flex;align-items:center;justify-content:center;gap:12px}
  .lockup__org{display:flex;align-items:center;gap:6px;font-family:"Jost",sans-serif;font-weight:500;color:var(--purple);font-size:15px;line-height:1.05;text-transform:uppercase;text-align:right;white-space:nowrap}
  .lockup__dot{width:11px;height:11px;border-radius:50%;background:var(--purple);flex:none}
  .lockup__rule{width:1px;background:var(--purple);flex:none}
  .lockup__program{font-family:"Jost",sans-serif;font-weight:500;color:var(--purple);text-transform:uppercase;line-height:1.05;white-space:nowrap}

  .card--front .lockup{height:157px}
  .card--front .lockup__rule{height:90px}
  .card--front .lockup__program{font-size:20px}
  .card--back .lockup{height:122px;padding-top:6px}
  .card--back .lockup__rule{height:62px}
  .card--back .lockup__org{font-size:13px}
  .card--back .lockup__program{font-size:17px}

  /* front */
  .tagline{position:absolute;top:157px;left:0;width:100%;height:142px;background:var(--purple);color:var(--white);font-family:"Jost",sans-serif;font-weight:500;padding:22px 0 0 28px;text-transform:uppercase}
  .tagline__line{display:block;font-size:27px;line-height:36px;white-space:nowrap}
  .tagline__line--small{font-size:21.5px}
  .hero{position:absolute;top:315px;left:0;width:100%;height:589px;background:linear-gradient(160deg,#d9d3e1 0%,#b7a5cd 45%,#876aae 75%,#cfcbd4 100%)}
  .url-bar{position:absolute;left:0;bottom:0;width:100%;height:51px;display:flex;align-items:center;justify-content:center;gap:9px;color:var(--white);font-family:"Jost",sans-serif;font-size:20px;white-space:nowrap}
  .card--front .url-bar{background:rgba(110,110,110,.8)}
  .card--back .url-bar{background:var(--purple)}
  .url-bar svg{width:14px;height:14px;flex:none}

  /* back */
  .intro{position:absolute;top:130px;left:19px;right:24px;font-size:13px;line-height:16px;text-align:justify}
  .features{position:absolute;top:197px;left:0;width:100%;list-style:none}
  .feature{position:relative;height:96px;margin-bottom:5px;background:linear-gradient(90deg,var(--row-alt),var(--row));display:flex}
  .feature__letter{position:absolute;left:18px;top:12px;font-family:"Jost",sans-serif;font-size:17px;color:var(--ink)}
  .feature__icon{position:absolute;left:44px;top:22px;width:52px;height:52px}
  .feature__desc{position:absolute;left:120px;top:4px;bottom:4px;right:13px;border-left:1.5px dashed var(--purple);padding-left:11px;display:flex;align-items:center;font-size:11.4px;line-height:14.5px;text-align:justify;color:#444}
  .more{position:absolute;top:808px;width:100%;text-align:center;font-family:"Jost",sans-serif;font-size:23px;color:var(--ink)}
</style>
</head>
<body>

<!-- Front side -->
<section class="card card--front">
  <header class="lockup">
    <div class="lockup__org"><span class="lockup__dot"></span><span>Skinward<br>Foundation</span></div>
    <span class="lockup__rule"></span>
    <div class="lockup__program">Dermal Care<br>Nursing Circle</div>
  </header>
  <h1 class="tagline">
    <span class="tagline__line">Inspired by patients</span>
    <span class="tagline__line tagline__line--small">Empowered by knowledge</span>
    <span class="tagline__line">Impacting melanoma</span>
  </h1>
  <div class="hero" role="img" aria-label="Photo: a smiling patient on crutches walking down a hospital corridor with a nurse in purple scrubs"></div>
  <footer class="url-bar">
    <svg viewBox="0 0 16 16" fill="none" stroke="currentColor" stroke-width="1.3"><circle cx="8" cy="8" r="6.8"/><ellipse cx="8" cy="8" rx="3" ry="6.8"/><path d="M1.2 8h13.6M2.2 4.6h11.6M2.2 11.4h11.6"/></svg>
    <span>www.DermalCareNurse.example</span>
  </footer>
</section>

<!-- Back side -->
<section class="card card--back">
  <header class="lockup">
    <div class="lockup__org"><span class="lockup__dot"></span><span>Skinward<br>Foundation</span></div>
    <span class="lockup__rule"></span>
    <div class="lockup__program">Dermal Care<br>Nursing Circle</div>
  </header>
  <p class="intro">You wear many hats and take care of patients with many different tumor types. Check out DermalCareNurse.example for free access to:</p>

  <ol class="features">
    <li class="feature">
      <span class="feature__letter">A.</span>
      <svg class="feature__icon" viewBox="0 0 52 52" fill="none" stroke="#2d2d2d" stroke-width="3"><rect x="4" y="7" width="42" height="38" rx="4"/><path d="M10 15h30"/><rect x="10" y="22" width="13" height="15" fill="#2d2d2d"/><path d="M28 24h12M28 30h12M28 36h12"/></svg>
      <p class="feature__desc">Hot off the press! Articles from the Journal of Clinical Skin Nursing outlining practical strategies to manage side-effects and promote adherence to melanoma therapies</p>
    </li>
    <li class="feature">
      <span class="feature__letter">B.</span>
      <svg class="feature__icon" viewBox="0 0 52 52" fill="#2d2d2d"><rect x="4" y="36" width="44" height="7" rx="3.5"/><rect x="20" y="10" width="12" height="22" rx="3"/><rect x="14" y="18" width="24" height="6" rx="3"/></svg>
      <p class="feature__desc">Visual and text-based therapeutic side effect management tools</p>
    </li>
    <li class="feature">
      <span class="feature__letter">C.</span>
      <svg class="feature__icon" viewBox="0 0 52 52" fill="#2d2d2d"><circle cx="26" cy="26" r="22"/><path d="M22 14h8v8h8v8h-8v8h-8v-8h-8v-8h8z" fill="#ececec"/></svg>
      <p class="feature__desc">A Nurse’s Toolkit with extensive melanoma nursing care resources</p>
    </li>
    <li class="feature">
      <span class="feature__letter">D.</span>
      <svg class="feature__icon" viewBox="0 0 52 52" fill="none" stroke="#2d2d2d" stroke-width="3"><rect x="7" y="5" width="30" height="42" rx="2"/><path d="M13 14h18M13 21h18M13 28h12M13 38h8"/><path d="M44 16 30 38l-2 6 5-4 14-22z" fill="#2d2d2d"/></svg>
      <p class="feature__desc">Printable patient resources to provide patients, organized by therapy</p>
    </li>
    <li class="feature">
      <span class="feature__letter">E.</span>
      <svg class="feature__icon" viewBox="0 0 52 52" fill="none" stroke="#2d2d2d" stroke-width="2"><circle cx="26" cy="26" r="23"/><circle cx="26" cy="26" r="18"/><circle cx="26" cy="26" r="6"/><circle cx="15" cy="20" r="2.5"/><circle cx="36" cy="18" r="2.5"/><circle cx="35" cy="34" r="2.5"/><circle cx="17" cy="34" r="2.5"/></svg>
      <p class="feature__desc">An oncology nurse community forum to share successes, challenges, insights, and solutions</p>
    </li>
    <li class="feature">
      <span class="feature__letter">F.</span>
      <svg class="feature__icon" viewBox="0 0 52 52" fill="none" stroke="#2d2d2d" stroke-width="3.5" stroke-linejoin="round"><path d="M26 14c-6-4-13-5-20-4v30c7-1 14 0 20 4 6-4 13-5 20-4V10c-7-1-14 0-20 4z"/><path d="M26 14v30"/></svg>
      <p class="feature__desc">Online educational modules, newsfeeds, and other material to keep you up to date</p>
    </li>
  </ol>

  <p class="more">And much more!</p>

  <footer class="url-bar">
    <svg viewBox="0 0 16 16" fill="none" stroke="currentColor" stroke-width="1.3"><circle cx="8" cy="8" r="6.8"/><ellipse cx="8" cy="8" rx="3" ry="6.8"/><path d="M1.2 8h13.6M2.2 4.6h11.6M2.2 11.4h11.6"/></svg>
    <span>www.DermalCareNurse.example</span>
  </footer>
</section>

</body>
</html>
```